Website: BrightHarbor Business Consultants, Qianhai SEZ, China

Our client is a business consultancy firm and will be the first to set up in the Qianhai Shenzhen-Hong Kong Modern Service Industry Cooperation Zone, China So we need a corporate website concept that engages service, finance and technology sector companies. The company can provide all the necessary services needed to set up shop in Qianhai. They are looking for a modern, international, reliable and strong image.

Here are some websites for reference prupose:

http://www.vornelpax.com/ (we like the dynamic banner and clear, clean layout of this website)

http://www.quilbrenadvisory.com/ (we like the background city image, use of light font, hover over menu functions and color scheme - purple and grey)

http://www.dovu.com/ (we like the simplicity of this website, clear lines and we like the dynamic banner)
Updates

Hello, We are currently undecided between three logo designs.  All three have been uploaded to the design brief so that you can use them as reference for the website design. Thx

Also please take note of the addition menu selection 'About Qianhai'. Thx

Hello all Designers, First of all we want thank you for participating in our website competition, the calibre of design was high and we appreciated the expedience. Our company is Lumen Harvest Web Design and Internet Marketing based in Shenzhen, China. We anticipate rapid growth in the Chinese domestic market as the country shifts in to a service sector economy. We hope to continue building reliable working relationships with you based on idea sharing and constructive feedback. Once again, Thankyou, LH Team

Target Market(s)

International finance and technology companies looking to set up in Qianhai Special Economic Zone, China

Industry/Entity Type

Finance

Requirements
Must have
• Initial design for home page and in later selection stages a secondary page will be required.

The design should be for PSD concepts only no code!

Menu bar, Photo banner -
A. Photo banner and text overlay,
B.Photo Banner and text description to left or right.

Social Connect icons, Site search bar (top right), Logo space (top left).

Menu bar at top with Home, About Us, About Qianhai, Services, Portfolio, Partners, Our Team Contact Us.

Standard 3-4 box layout - Banner at top and 2-3 boxes under banner.

Colour scheme- A. Purple and Blue, must have light background/body
B. Shades of white, black and grey.

Simple, clear, clean, sharp.

```html
<!DOCTYPE html>
<html lang="en">
<head>
<meta charset="utf-8">
<title>BrightHarbor Business Consultants</title>
<link rel="stylesheet" href="https://fonts.googleapis.com/css2?family=Source+Sans+3:wght@300;400;600&family=PT+Sans+Narrow:wght@400;700&display=swap">
<style>
  :root {
    --magenta: #b8168f;
    --magenta-dark: #9d0f7a;
    --plum: #5e2a58;
    --blue: #1a86b6;
    --berry: #9a1b6c;
    --ink: #333333;
    --text: #555555;
    --muted: #8a8a8a;
    --rule: #dddddd;
    --footer: #f3f3f3;
    --page: #ffffff;
  }
  * { box-sizing: border-box; margin: 0; padding: 0; }
  html, body { width: 1105px; height: 1200px; overflow: hidden; background: var(--page); }
  body { position: relative; font-family: "Source Sans 3", sans-serif; color: var(--text); }

  .header-glow { position: absolute; left: 22px; top: 0; width: 1060px; height: 398px;
    background: linear-gradient(#ffffff, #f6f6f7 70%, #ffffff); }

  .brand { position: absolute; left: 73px; top: 40px; display: flex; align-items: center; gap: 14px; }
  .brand-dot { width: 58px; height: 58px; border-radius: 50%; background: var(--magenta); }
  .brand-name { font-family: "Source Sans 3", sans-serif; font-weight: 600; font-size: 34px; color: #222; letter-spacing: 1px; }

  .social { position: absolute; left: 920px; top: 37px; display: flex; gap: 5px; }
  .social span { width: 23px; height: 23px; border-radius: 3px; background: #5b9bd5; }
  .social span:nth-child(2) { background: #2a78b5; }
  .social span:nth-child(3) { background: #3b5998; }
  .social span:nth-child(4) { background: #3f7fd0; }

  .search { position: absolute; left: 772px; top: 70px; width: 253px; height: 32px; border: 1px solid #d5d5d5; background: #fff; }
  .search-field { position: absolute; left: 12px; top: 7px; font-style: italic; font-size: 13px; color: #999; }
  .search-icon { position: absolute; right: 10px; top: 7px; }

  .main-nav { position: absolute; left: 73px; top: 119px; width: 958px; height: 50px;
    background: linear-gradient(var(--magenta), var(--magenta-dark)); display: flex; align-items: center; justify-content: center; }
  .main-nav a { color: #fff; text-decoration: none; font-size: 17px; font-weight: 400; padding: 0 18px; border-left: 1px solid rgba(255,255,255,.5); line-height: 18px; }
  .main-nav a:first-child { border-left: none; }

  .hero { position: absolute; left: 73px; top: 169px; width: 958px; height: 354px; overflow: hidden; }
  .hero-photo { position: absolute; inset: 0; background: linear-gradient(90deg, #c9cdd2, #eceff1 35%, #dfe2e6 60%, #b9b5bd); }
  .hero-panel { position: absolute; right: 0; top: 0; }
  .hero-copy { position: absolute; left: 650px; top: 62px; width: 290px; color: #fff; }
  .hero-kicker { font-family: "PT Sans Narrow", sans-serif; font-size: 20px; letter-spacing: .3px; }
  .hero-title { font-family: "PT Sans Narrow", sans-serif; font-size: 36px; line-height: 40px; margin-top: 2px; }
  .hero-text { font-size: 13px; line-height: 23.5px; margin-top: 6px; font-weight: 300; }
  .hero-thumbs { display: flex; gap: 8px; margin-top: 17px; }
  .hero-thumbs span { width: 60px; height: 52px; border: 2px solid #fff; background: linear-gradient(#d8d2cf, #9e97a3); }
  .hero-arrows { margin-top: 20px; }

  .welcome { position: absolute; left: 73px; top: 560px; width: 632px; }
  .section-title { font-family: "PT Sans Narrow", sans-serif; font-size: 26px; color: var(--blue); font-weight: 400; }
  .lead { font-size: 15px; line-height: 24px; color: var(--ink); margin-top: 4px; }
  .body-text { font-size: 12.5px; line-height: 23.5px; margin-top: 6px; font-weight: 300; color: var(--text); }

  .rule { position: absolute; height: 1px; background: var(--rule); }

  .projects { position: absolute; left: 75px; top: 762px; width: 620px; }
  .projects-title { font-family: "PT Sans Narrow", sans-serif; font-size: 22px; color: var(--berry); font-weight: 400; }
  .project-list { display: flex; gap: 10px; margin-top: 8px; }
  .project { width: 199px; }
  .project-photo { height: 98px; border-radius: 3px; background: linear-gradient(135deg, #d9dde1, #7f8a96); }
  .project:nth-child(2) .project-photo { background: linear-gradient(135deg, #c9ccd0, #3e4248); }
  .project:nth-child(3) .project-photo { background: linear-gradient(135deg, #dfe6ec, #8fb0cc); }
  .project-title { font-size: 15px; color: var(--ink); margin-top: 15px; padding-left: 3px; }
  .project-text { font-size: 12.5px; line-height: 21px; margin-top: 3px; padding-left: 3px; font-weight: 300; }

  .services { position: absolute; left: 739px; top: 561px; width: 293px; }
  .services .section-title { font-size: 23px; }
  .service-photo { height: 104px; margin: 8px 0 0 2px; width: 283px; background: linear-gradient(90deg, #e3e6ea, #a7b6c6 60%, #5d6b78); }
  .service-title { font-size: 15px; color: var(--ink); margin: 12px 0 0 3px; }
  .service-text { font-size: 12.5px; line-height: 21px; margin: 5px 0 0 3px; font-weight: 300; }

  .portfolio { position: absolute; left: 741px; top: 848px; width: 290px; }
  .portfolio .section-title { font-size: 23px; }
  .portfolio-grid { display: grid; grid-template-columns: repeat(3, 85px); grid-auto-rows: 69px; column-gap: 13px; row-gap: 15px; margin-top: 12px; }
  .portfolio-grid span { background: linear-gradient(#c7ccd2, #8c96a0); }
  .portfolio-grid span:nth-child(1) { background: linear-gradient(#2b7fc4, #0f4d8a); }
  .portfolio-grid span:nth-child(2) { background: linear-gradient(#f1e6e0, #c99a85); }
  .portfolio-grid span:nth-child(3) { background: linear-gradient(#f0f0f0, #2c2c2c); }
  .portfolio-grid span:nth-child(5) { background: linear-gradient(#a8c4e6, #5b6f86); }
  .portfolio-grid span:nth-child(6) { background: linear-gradient(#eeeeee, #b5b0a8); }

  .site-footer { position: absolute; left: 0; top: 1089px; width: 1105px; height: 64px; background: linear-gradient(#ececec, var(--footer) 40%, #fafafa); }
  .copyright { position: absolute; left: 74px; top: 30px; font-size: 12px; color: var(--muted); font-weight: 300; }
  .footer-nav { position: absolute; right: 82px; top: 27px; font-size: 14px; color: #444; }
  .footer-nav a { color: inherit; text-decoration: none; }
  .footer-nav i { font-style: normal; padding: 0 5px; }
</style>
</head>
<body>
  <div class="header-glow"></div>

  <header>
    <div class="brand">
      <span class="brand-dot"></span>
      <span class="brand-name">BRIGHTHARBOR</span>
    </div>
    <div class="social" aria-label="Social links"><span></span><span></span><span></span><span></span></div>
    <div class="search">
      <span class="search-field">Search here..</span>
      <svg class="search-icon" width="18" height="18" viewBox="0 0 18 18"><circle cx="7.5" cy="7.5" r="5.5" fill="none" stroke="#888" stroke-width="2.4"/><line x1="11.5" y1="11.5" x2="16" y2="16" stroke="#888" stroke-width="3" stroke-linecap="round"/></svg>
    </div>
  </header>

  <nav class="main-nav">
    <a href="#">HOME</a><a href="#">ABOUT US</a><a href="#">ABOUT QIANHAI</a><a href="#">SERVICES</a><a href="#">PORTFOLIO</a><a href="#">PARTNERS</a><a href="#">OUR TEAM</a><a href="#">CONTACT US</a>
  </nav>

  <section class="hero">
    <div class="hero-photo" role="img" aria-label="Consultant presenting an organisation chart on a flip chart to colleagues"></div>
    <svg class="hero-panel" width="340" height="354" viewBox="0 0 340 354"><path d="M40 0 H340 V354 H0 C20 250 20 90 40 0 Z" fill="var(--plum)"/></svg>
    <div class="hero-copy">
      <p class="hero-kicker">EXPERT CONSULTANTS FOR</p>
      <h1 class="hero-title">BUSINESS GROWTH</h1>
      <p class="hero-text">Nunc tempus felis vitae urna. Vivamus porttitor, g, purus nisi eleifend libero a tempus libero lectus feugiat felis. Morbi diam mauris</p>
      <div class="hero-thumbs">
        <span role="img" aria-label="Team member portrait"></span>
        <span role="img" aria-label="Team member portrait"></span>
        <span role="img" aria-label="Team member portrait"></span>
        <span role="img" aria-label="Team member portrait"></span>
      </div>
      <svg class="hero-arrows" width="44" height="24" viewBox="0 0 44 24"><path d="M14 2 L4 12 L14 22 M30 2 L40 12 L30 22" fill="none" stroke="#fff" stroke-width="2"/></svg>
    </div>
  </section>

  <section class="welcome">
    <h2 class="section-title">WELCOME TO OUR WEBSITE MAINPAGE</h2>
    <p class="lead">Nunc tempus felis vitae urna. Vivamus porttitor, g, purus nisi eleifend libero, a tempus libero lectus feugiat felis. Morbi diam mauris, viverra in, gravida eu, mattis in, ante</p>
    <p class="body-text">Cum sociis natoque penatibus et magnis dis parturient montes, nascetur ridiculus mus. In iaculis facilisis massa. Etiam eu urna. Sed porta. Suspendisse quam leo, molestie sed, luctus quis, feugiat in, pede. Fusce tellus. Sed metus augue, convallis et, vehicula ut, pulvinar eu, ante. Integer orci tellus, tristique vitae, consequat nec, porta vel, lectus.</p>
  </section>

  <div class="rule" style="left:74px; top:745px; width:620px;"></div>

  <section class="projects">
    <h2 class="projects-title">Recent Projects</h2>
    <div class="project-list">
      <article class="project">
        <div class="project-photo" role="img" aria-label="Business team meeting around a table"></div>
        <h3 class="project-title">Project Tittle</h3>
        <p class="project-text">Vivamus porttitor, g, purus nisi eleifend libero, a tempus libero lectus feugiat felis. Morbi diam mauris, viverra&nbsp; gravida eu</p>
      </article>
      <article class="project">
        <div class="project-photo" role="img" aria-label="Group of business professionals standing together"></div>
        <h3 class="project-title">Project Tittle</h3>
        <p class="project-text">Vivamus porttitor, g, purus nisi eleifend libero, a tempus libero lectus feugiat felis. Morbi diam mauris, viverra</p>
      </article>
      <article class="project">
        <div class="project-photo" role="img" aria-label="Businessman working at a laptop"></div>
        <h3 class="project-title">Project Tittle</h3>
        <p class="project-text">Purus nisi eleifend libero, a tempus libero lectus feugiat felis. Morbi diam mauris, viverra&nbsp; gravida eu</p>
      </article>
    </div>
  </section>

  <aside class="services">
    <h2 class="section-title">SERVICES WE PROVIDE</h2>
    <div class="service-photo" role="img" aria-label="Colleagues in a friendly business discussion"></div>
    <h3 class="service-title">Phasellus felis dolor scelerisque</h3>
    <p class="service-text">Tempus eget, lobortis id, libero. Donec scelerisque leo ac risus. Praesent sit amet est. In dictum, dolor eu dictum porttitor, enim felis viverra mi</p>
  </aside>

  <div class="rule" style="left:739px; top:823px; width:293px;"></div>

  <aside class="portfolio">
    <h2 class="section-title">PORTFOLIO</h2>
    <div class="portfolio-grid">
      <span role="img" aria-label="Blue digital network graphic"></span>
      <span role="img" aria-label="Stacked hands in teamwork"></span>
      <span role="img" aria-label="Business handshake"></span>
      <span role="img" aria-label="Business colleagues in office"></span>
      <span role="img" aria-label="City skyline with globe"></span>
      <span role="img" aria-label="Consultants reviewing documents"></span>
    </div>
  </aside>

  <footer class="site-footer">
    <p class="copyright">Copyright © 2013 Company Name.&nbsp; All right reserved.&nbsp; Term of Use</p>
    <nav class="footer-nav">
      <a href="#">Home</a><i>|</i><a href="#">About Us</a><i>|</i><a href="#">About Qianhai</a><i>|</i><a href="#">Services</a><i>|</i><a href="#">Portfolio</a><i>|</i><a href="#">Partners</a><i>|</i><a href="#">Our Team</a><i>|</i><a href="#">Contact Us</a>
    </nav>
  </footer>
</body>
</html>
```